Elevating our current Business Card Design

We want to elevate our current business card with a new design to look like a zenith 300 company. We are a premium lubricant distributor (oil and grease).
We need 2 versions, version 1 is as per the uploaded a copy of our current business card with the English version.
For our Chinese version we need to use the front to be English in English and have the back of the card designed exactly like the front for all info to be in Chinese.
The design template needs to be such that we can amend the template with adding different information for each person's card.
The background colour of the card can be changed- we just need to clearly see all information on the card and logos.
The QJR and Ember steady logos cannot have any colour or display changes- only use the logos attached.
All logos need to be included and all information from the attached current card

```html
<!DOCTYPE html>
<html lang="en">
<head>
<meta charset="utf-8">
<title>Northcrest Lubricant Partners – Business Card</title>
<link rel="stylesheet" href="https://fonts.googleapis.com/css2?family=Open+Sans:wght@400;600;700;800&family=Exo+2:ital,wght@1,700&display=swap">
<style>
  :root{
    --stage:#232323;
    --card:#1c1c1f;
    --ink:#ffffff;
    --brand-red:#e8292a;
    --deep-red:#b51c22;
    --placeholder:#4a4a50;
  }
  *{box-sizing:border-box;margin:0;padding:0}
  html,body{width:1200px;height:780px;overflow:hidden;background:var(--stage)}
  body{font-family:"Open Sans",Arial,sans-serif;color:var(--ink);position:relative}

  .card{position:absolute;top:230px;width:560px;height:320px;background:var(--card);
        border-radius:18px;overflow:hidden;box-shadow:0 18px 40px rgba(0,0,0,.45)}
  .card--front{left:20px}
  .card--back{left:620px;display:flex;align-items:center;justify-content:center}

  .brand{position:absolute;left:34px;top:26px;display:flex;align-items:center;gap:10px}
  .brand__dot{width:24px;height:24px;border-radius:50%;background:var(--brand-red)}
  .brand__name{font-weight:800;font-size:24px;letter-spacing:.5px;color:var(--ink)}

  .address{position:absolute;left:34px;top:74px;font-size:13px;line-height:18px;font-style:normal}
  .contacts{position:absolute;left:34px;top:118px;list-style:none;font-size:13px;line-height:19px}
  .contacts li{display:flex;align-items:center;gap:8px}
  .contacts svg{width:12px;height:12px;flex:none}

  .person{position:absolute;right:40px;top:124px;text-align:right}
  .person__name{font-family:"Exo 2",sans-serif;font-style:italic;font-weight:700;
                font-size:32px;color:var(--brand-red);line-height:1}
  .person__title{font-size:15px;margin-top:6px;letter-spacing:.3px}
  .edge-steps{position:absolute;right:0;top:112px;width:18px;height:86px}

  .credentials{position:absolute;left:34px;bottom:22px;right:40px;display:flex;align-items:flex-end;gap:14px}
  .ember{display:flex;align-items:center;gap:6px;margin-bottom:8px}
  .ember__ring{width:22px;height:22px;border-radius:50%;border:3px solid var(--ink)}
  .ember__name{font-size:12px;font-weight:700;line-height:1.05;width:52px}

  .partner{display:flex;height:58px;border:2px solid var(--brand-red);border-radius:4px;overflow:hidden}
  .partner__brand{display:flex;align-items:center;gap:6px;padding:0 10px}
  .partner__dot{width:10px;height:10px;background:var(--brand-red)}
  .partner__name{font-size:11px;font-weight:700;color:var(--brand-red)}
  .partner__supply{background:var(--brand-red);display:flex;align-items:center;padding:0 12px}
  .partner__supply span{font-size:14px;font-weight:800;color:var(--ink);letter-spacing:.6px}

  .cert{width:44px;height:44px;border-radius:50%;background:var(--placeholder);margin-bottom:6px}

  .back-brand{display:flex;align-items:center;gap:18px}
  .back-brand__dot{width:64px;height:64px;border-radius:50%;background:var(--brand-red)}
  .back-brand__name{font-size:54px;font-weight:800;letter-spacing:1px}
</style>
</head>
<body>

<section class="card card--front" aria-label="Card front">
  <div class="brand"><span class="brand__dot"></span><span class="brand__name">NORTHCREST</span></div>

  <address class="address">48 Harbour Freight Road<br>Belmont, WA 6104</address>

  <ul class="contacts">
    <li><svg viewBox="0 0 12 12"><path d="M2 1h3l1 3-2 1a7 7 0 0 0 3 3l1-2 3 1v3c-6 0-9-3-9-9z" fill="var(--brand-red)"/></svg>1300 472 615</li>
    <li><svg viewBox="0 0 12 12"><rect x="3" y="0.5" width="6" height="11" rx="1" fill="none" stroke="var(--brand-red)"/></svg>+61 400 218 374</li>
    <li><svg viewBox="0 0 12 12"><rect x="1" y="4" width="10" height="7" rx="1" fill="var(--brand-red)"/><rect x="3" y="1" width="6" height="4" fill="var(--brand-red)"/></svg>+61 8 9000 4521</li>
    <li><svg viewBox="0 0 12 12"><circle cx="6" cy="6" r="5" fill="none" stroke="var(--brand-red)"/><path d="M1 6h10M6 1c-3 3-3 7 0 10M6 1c3 3 3 7 0 10" fill="none" stroke="var(--brand-red)"/></svg>www.northcrestdirect.com</li>
    <li><svg viewBox="0 0 12 12"><rect x="1" y="2.5" width="10" height="7" rx="1" fill="var(--brand-red)"/><path d="M1.5 3l4.5 3.5L10.5 3" fill="none" stroke="var(--card)"/></svg>marina.delcourt@northcrestdirect.com</li>
  </ul>

  <div class="person">
    <p class="person__name">Marina Delcourt</p>
    <p class="person__title">Administration Executive</p>
  </div>
  <svg class="edge-steps" viewBox="0 0 18 86" aria-hidden="true">
    <rect x="0" y="0" width="18" height="34" fill="var(--brand-red)"/>
    <rect x="5" y="34" width="13" height="26" fill="var(--deep-red)"/>
    <rect x="10" y="60" width="8" height="26" fill="var(--brand-red)"/>
  </svg>

  <div class="credentials">
    <div class="ember"><span class="ember__ring"></span><span class="ember__name">Ember steady</span></div>
    <div class="partner">
      <div class="partner__brand"><span class="partner__dot"></span><span class="partner__name">NORTHCREST</span></div>
      <div class="partner__supply"><span>ORVANE</span></div>
    </div>
    <div class="cert" role="img" aria-label="Certification badge placeholder"></div>
    <div class="cert" role="img" aria-label="Certification badge placeholder"></div>
    <div class="cert" role="img" aria-label="Certification badge placeholder"></div>
  </div>
</section>

<section class="card card--back" aria-label="Card back">
  <div class="back-brand"><span class="back-brand__dot"></span><span class="back-brand__name">NORTHCREST</span></div>
</section>

</body>
</html>
```